Business card design for new eCommerce site focusing on integrity and strong businsess tactics

We need a business card that will stand out and be memorable. Something with color that matches our company logo colors. Think high end version of Pactivo. There are 2 logos provided. The parent company is called Amber Ledge Partners and we are presenting a new and very exciting eCommerce site called BrightHarborTrade.example.

Target Market(s)

Our target markets are in the Activities, Food and Beverage, Health and Beauty

Industry/Entity Type

Marketing

Contact Information for Business Card

We have 4 members that need cards...I will provide all info to the winner of the design contest
Business Address is
4870 West 63rd Avenue, Suite C207
Phoenix AZ 85731

Font styles to use
Serif
Sans Serif

Colors

Designer to choose colors to be used in the design.

Requirements
Must have
• The card must be memorable...should be unique in design but must exude integrity and be playful .
• I have provided several colors or our parent company...please feel free to use which ever
Nice to have
• I will leave this up to you. Feel free to use other images of your choosing that wraps around our client.....Activities, Dining, Health, Beauty
Should not have
• just dont be boring

```html
<!DOCTYPE html>
<html lang="en">
<head>
<meta charset="utf-8">
<title>BrightHarborTrade.example and Amber Ledge Partners business card</title>
<link rel="stylesheet" href="https://fonts.googleapis.com/css2?family=Montserrat:wght@600;700&family=Open+Sans:wght@400;600&display=swap">
<style>
  :root {
    --backdrop: #2a2a2c;
    --card: #ffffff;
    --card-shade: #eeeff1;
    --navy: #14204a;
    --green: #6aa93a;
    --ink: #1c1c22;
    --muted: #6b6f78;
    --rule: #3a3d46;
  }
  html, body {
    margin: 0;
    width: 1200px;
    height: 904px;
    overflow: hidden;
    background: var(--backdrop);
  }
  .canvas {
    position: relative;
    width: 1200px;
    height: 904px;
  }
  .card {
    position: absolute;
    width: 520px;
    height: 298px;
    background: linear-gradient(135deg, var(--card) 0%, var(--card-shade) 100%);
    box-shadow: 0 14px 30px rgba(0,0,0,.45);
    overflow: hidden;
  }
  .card-front { left: 90px; top: 150px; }
  .card-back { left: 590px; top: 450px; }

  .brand {
    position: absolute;
    left: 48px;
    top: 128px;
    display: flex;
    align-items: center;
    gap: 12px;
  }
  .brand-dot {
    width: 26px;
    height: 26px;
    border-radius: 50%;
    background: var(--green);
    flex: none;
  }
  .brand-name {
    font-family: "Montserrat", sans-serif;
    font-weight: 600;
    font-size: 22px;
    color: var(--green);
    line-height: 1;
  }
  .brand-tagline {
    position: absolute;
    left: 86px;
    top: 160px;
    font-family: "Open Sans", sans-serif;
    font-size: 12px;
    letter-spacing: .5px;
    color: var(--muted);
  }

  .band {
    position: absolute;
    left: 0;
    top: 40px;
    width: 100%;
    height: 42px;
    background: var(--navy);
  }
  .badge {
    position: absolute;
    left: 186px;
    top: 17px;
    width: 88px;
    height: 88px;
    border-radius: 50%;
    background: var(--card);
    display: flex;
    align-items: center;
    justify-content: center;
  }
  .badge-core {
    width: 74px;
    height: 74px;
    border-radius: 50%;
    background: var(--navy);
  }
  .company {
    position: absolute;
    left: 0;
    width: 460px;
    top: 114px;
    text-align: center;
    font-family: "Montserrat", sans-serif;
    font-weight: 700;
    font-size: 21px;
    color: var(--navy);
  }
  .person {
    position: absolute;
    left: 0;
    width: 500px;
    top: 152px;
    text-align: center;
    font-family: "Montserrat", sans-serif;
    color: var(--navy);
  }
  .person-name { font-weight: 700; font-size: 17px; display: block; }
  .person-role {
    font-family: "Open Sans", sans-serif;
    font-size: 12px;
    color: var(--ink);
    display: block;
    margin-top: 1px;
  }
  .address {
    position: absolute;
    right: 240px;
    top: 208px;
    text-align: right;
    font-family: "Open Sans", sans-serif;
    font-size: 13px;
    line-height: 20px;
    color: var(--ink);
  }
  .divider {
    position: absolute;
    left: 292px;
    top: 206px;
    width: 1px;
    height: 64px;
    background: var(--rule);
  }
  .contacts {
    position: absolute;
    left: 304px;
    top: 206px;
    margin: 0;
    padding: 0;
    list-style: none;
    font-family: "Open Sans", sans-serif;
    font-size: 12px;
    line-height: 21px;
    color: var(--ink);
  }
  .contacts li { display: flex; align-items: center; gap: 8px; }
  .contacts svg { width: 11px; height: 11px; flex: none; }
</style>
</head>
<body>
<main class="canvas">

  <section class="card card-front" aria-label="Card front">
    <div class="brand">
      <span class="brand-dot"></span>
      <span class="brand-name">BrightHarborTrade.example</span>
    </div>
    <div class="brand-tagline">Activities-Dining-Health-Beauty</div>
  </section>

  <section class="card card-back" aria-label="Card back">
    <div class="band"></div>
    <div class="badge"><div class="badge-core"></div></div>
    <div class="company">Amber Ledge Partners</div>
    <div class="person">
      <span class="person-name">Dana Whitfield</span>
      <span class="person-role">Manager</span>
    </div>
    <address class="address" style="font-style:normal">
      4870 West 63rd Avenue<br>
      Suite C207<br>
      Phoenix AZ 85731
    </address>
    <div class="divider"></div>
    <ul class="contacts">
      <li>
        <svg viewBox="0 0 12 12" aria-hidden="true"><path fill="var(--navy)" d="M2.5 1h2l1 2.8-1.3 1a6 6 0 0 0 2.9 2.9l1-1.3 2.9 1v2c0 .6-.5 1.1-1.1 1.1A9.4 9.4 0 0 1 1.4 2.1C1.4 1.5 1.9 1 2.5 1z"/></svg>
        +1 520 555 0148
      </li>
      <li>
        <svg viewBox="0 0 12 12" aria-hidden="true"><rect x="1" y="2.5" width="10" height="7" rx="1" fill="var(--navy)"/><path d="M1.5 3.2 6 6.6l4.5-3.4" fill="none" stroke="#fff" stroke-width="1"/></svg>
        info@brightharbortrade.example
      </li>
      <li>
        <svg viewBox="0 0 12 12" aria-hidden="true"><circle cx="6" cy="6" r="5" fill="var(--navy)"/><path d="M1 6h10M6 1c2 2.5 2 7.5 0 10M6 1c-2 2.5-2 7.5 0 10" fill="none" stroke="#fff" stroke-width=".8"/></svg>
        www.brightharbortrade.example
      </li>
    </ul>
  </section>

</main>
</body>
</html>
```